New Company Business Card design

Looking for a corporate looking business card utilising my new logo design - the logo i would like embossed as one option and flat as another - simplistic but stylish - less is more - we are an import export business launching into the market - i would like a couple of options as main background - Grey or Black

```html
<!DOCTYPE html>
<html lang="en">
<head>
<meta charset="utf-8">
<title>Kestrel Trade – Business Card Options</title>
<link href="https://fonts.googleapis.com/css2?family=Crimson+Text&display=swap" rel="stylesheet">
<style>
  :root {
    --charcoal: #333333;
    --paper: #dedede;
    --blue: #1174bd;
    --band-grey: #d2d2d2;
    --ink: #1f1f1f;
    --white: #ffffff;
    --icon-grey: #7a7a7a;
    --rule: #dcdcdc;
  }
  html, body {
    margin: 0;
    padding: 0;
    width: 1200px;
    height: 1200px;
    overflow: hidden;
    background: var(--white);
  }
  .sheet {
    position: relative;
    width: 1200px;
    height: 1200px;
    font-family: "Crimson Text", Georgia, serif;
  }
  .card {
    position: absolute;
    width: 570px;
    height: 340px;
    display: block;
  }
  .card--front-dark  { left: 17px;  top: 101px; }
  .card--back-dark   { left: 609px; top: 101px; }
  .card--front-light { left: 17px;  top: 725px; }
  .card--back-light  { left: 609px; top: 725px; }
  .divider {
    position: absolute;
    left: 34px;
    top: 601px;
    width: 1130px;
    height: 2px;
    background: var(--rule);
  }
  .card text { font-family: "Crimson Text", Georgia, serif; }
  .brand-name { fill: var(--blue); font-size: 40px; letter-spacing: 2px; }
  .contact { fill: var(--ink); font-size: 26px; }
  .holder-name { font-size: 33px; }
  .holder-name--on-dark, .tagline--on-dark { fill: var(--white); }
  .holder-name--on-blue, .tagline--on-blue { fill: var(--white); }
  .tagline { font-size: 33px; }
  .bg-dark { fill: var(--charcoal); }
  .bg-light { fill: var(--paper); }
  .accent { fill: var(--blue); }
  .strip { fill: var(--paper); }
  .band-grey { fill: var(--band-grey); }
  .icon-line { fill: none; stroke: var(--blue); stroke-width: 2.2; }
  .icon-fill { fill: var(--blue); }
  .avatar-dark { fill: none; stroke: var(--icon-grey); stroke-width: 2.5; }
  .avatar-light { fill: none; stroke: var(--white); stroke-width: 2.5; }
</style>
</head>
<body>
<main class="sheet">

  <!-- Front, charcoal -->
  <svg class="card card--front-dark" viewBox="0 0 713 425" aria-label="Front of card, charcoal option">
    <rect class="bg-dark" width="713" height="425"/>
    <polygon class="accent" points="362,0 713,0 713,285 446,285 366,188 445,188 373,100 440,100"/>
    <polygon class="strip" points="400,25 713,25 713,100 460,100"/>
    <polygon class="strip" points="400,110 713,110 713,185 465,185"/>
    <polygon class="strip" points="398,200 713,200 713,275 460,275"/>

    <g class="brand">
      <circle cx="187" cy="125" r="34" fill="none" stroke="var(--blue)" stroke-width="6"/>
      <text class="brand-name" x="187" y="210" text-anchor="middle">KESTREL TRADE</text>
    </g>

    <g class="contact-row">
      <circle class="icon-line" cx="480" cy="63" r="15"/>
      <path class="icon-fill" d="M474,55 l4,-2 3,6 -3,2 q2,5 6,7 l2,-3 6,3 -2,4 q-12,0 -16,-17z"/>
      <text class="contact" x="512" y="73">+1 555 0142</text>
    </g>
    <g class="contact-row">
      <rect class="icon-line" x="456" y="136" width="48" height="20" rx="3"/>
      <path class="icon-fill" d="M486,150 l3,15 3,-5 5,6 3,-2 -5,-6 6,-2z"/>
      <text class="contact" x="516" y="154">kestreltrade.com</text>
    </g>
    <g class="contact-row">
      <rect class="icon-fill" x="466" y="229" width="30" height="20"/>
      <path d="M466,229 l15,12 15,-12 M466,249 l11,-10 M496,249 l-11,-10" fill="none" stroke="var(--paper)" stroke-width="1.6"/>
      <text class="contact" x="516" y="247">info@kestrel.co</text>
    </g>

    <g class="holder">
      <circle class="avatar-dark" cx="70" cy="359" r="32"/>
      <path class="avatar-dark" d="M56,385 q0,-12 9,-15 q-9,-6 -9,-17 q0,-14 14,-14 q14,0 14,14 q0,11 -9,17 q9,3 9,15"/>
      <text class="holder-name holder-name--on-dark" x="138" y="370">Mr. Grey and Blue</text>
    </g>
  </svg>

  <!-- Back, charcoal -->
  <svg class="card card--back-dark" viewBox="0 0 713 425" aria-label="Back of card, charcoal option">
    <rect class="bg-dark" width="713" height="425"/>
    <polygon class="accent" points="0,0 142,185 59,188 132,277 713,277 713,295 0,295"/>
    <g class="brand">
      <circle cx="357" cy="130" r="34" fill="none" stroke="var(--blue)" stroke-width="6"/>
      <text class="brand-name" x="357" y="215" text-anchor="middle">KESTREL TRADE</text>
    </g>
    <text class="tagline tagline--on-dark" x="349" y="370" text-anchor="middle">Import Export Business Launching</text>
  </svg>

  <div class="divider"></div>

  <!-- Front, light -->
  <svg class="card card--front-light" viewBox="0 0 713 425" aria-label="Front of card, light grey option">
    <rect class="bg-light" width="713" height="425"/>
    <polygon class="accent" points="362,0 713,0 713,285 446,285 366,188 445,188 373,100 440,100"/>
    <polygon class="strip" points="400,25 713,25 713,100 460,100"/>
    <polygon class="strip" points="400,110 713,110 713,185 465,185"/>
    <polygon class="strip" points="398,200 713,200 713,277 460,277"/>
    <rect class="accent" x="0" y="277" width="713" height="148"/>

    <g class="brand">
      <circle cx="187" cy="125" r="34" fill="none" stroke="var(--blue)" stroke-width="6"/>
      <text class="brand-name" x="187" y="210" text-anchor="middle">KESTREL TRADE</text>
    </g>

    <g class="contact-row">
      <circle class="icon-line" cx="480" cy="63" r="15"/>
      <path class="icon-fill" d="M474,55 l4,-2 3,6 -3,2 q2,5 6,7 l2,-3 6,3 -2,4 q-12,0 -16,-17z"/>
      <text class="contact" x="512" y="73">+1 555 0142</text>
    </g>
    <g class="contact-row">
      <rect class="icon-line" x="456" y="136" width="48" height="20" rx="3"/>
      <path class="icon-fill" d="M486,150 l3,15 3,-5 5,6 3,-2 -5,-6 6,-2z"/>
      <text class="contact" x="516" y="154">kestreltrade.com</text>
    </g>
    <g class="contact-row">
      <rect class="icon-fill" x="466" y="229" width="30" height="20"/>
      <path d="M466,229 l15,12 15,-12 M466,249 l11,-10 M496,249 l-11,-10" fill="none" stroke="var(--paper)" stroke-width="1.6"/>
      <text class="contact" x="516" y="247">info@kestrel.co</text>
    </g>

    <g class="holder">
      <circle class="avatar-light" cx="70" cy="359" r="32"/>
      <path class="avatar-light" d="M56,385 q0,-12 9,-15 q-9,-6 -9,-17 q0,-14 14,-14 q14,0 14,14 q0,11 -9,17 q9,3 9,15"/>
      <text class="holder-name holder-name--on-blue" x="138" y="370">Mr. Grey and Blue</text>
    </g>
  </svg>

  <!-- Back, light -->
  <svg class="card card--back-light" viewBox="0 0 713 425" aria-label="Back of card, light grey option">
    <rect class="bg-light" width="713" height="425"/>
    <polygon class="accent" points="0,0 142,185 59,188 132,277 0,277"/>
    <rect class="band-grey" x="0" y="277" width="713" height="19"/>
    <rect class="accent" x="0" y="296" width="713" height="129"/>
    <g class="brand">
      <circle cx="370" cy="125" r="34" fill="none" stroke="var(--blue)" stroke-width="6"/>
      <text class="brand-name" x="370" y="210" text-anchor="middle">KESTREL TRADE</text>
    </g>
    <text class="tagline tagline--on-blue" x="349" y="370" text-anchor="middle">Import Export Business Launching</text>
  </svg>

</main>
</body>
</html>
```